Brightway Haus Inc. Business Card Design

Brightway Haus Inc. is in search of a great clean design for our business cards!

Looking to incorporate our full logo and watermark on side one (however, I am open to having the text and watermark separated within the design.)

On side two, I am looking to have contact information (Name, Position, Phone #, Email, Website (www.thebrightwayhaus.ca). Can have the logo and/or watermark as part of the design if applicable.

Please add tagline "Where Shine Counts" on either side 1 or 2. This tagline can be in a sans serif, serif or cursive font as long as it compliments overall design. Capitalization can be title or sentence case depending on how it fits within the design.

Get creative!! Looking for a clean, crisp, premium design! Looking for a glossy card finish with spot UV features when printed. Cards will also be printed with rounded corners. Standard dimensions (3.5 x 2).

Target Market(s)

B2B - primary clients are business owners or property management corporations. (residential jobs are few and far between)

Industry/Entity Type

Business

Contact Information for Business Card

- clean, crisp design
- double sided
- spot UV accents and glossy finish upon printing
- standard business card size (3.5 x 2) with rounded corners
- please see project description for requirements per side

Font styles to use
Sans Serif

Requirements
Must have
• - adequate bleeds with print ready files
• - cohesive design elements between side 1 & 2
• - spot UV elements (can be on both sides or just one, use your discretion)
• - colour pallet should match the logo file provided
• - incorporate tagline "where shine counts" (this tagline can be in a serif or sans serif font as long as it is complimentary to the overall design.
Nice to have
• - Premium elements with a clean design
Should not have
• - Please omit cartoon or whimsical like designs, think premium.
• - Colours should not stray from the pallet of the provided logo.

```html
<!DOCTYPE html>
<html lang="en">
<head>
<meta charset="utf-8">
<title>Brightway Haus Inc. Business Card</title>
<link href="https://fonts.googleapis.com/css2?family=Roboto:ital,wght@0,400;0,700;1,400&family=Roboto+Condensed:wght@400;700&display=swap" rel="stylesheet">
<style>
  :root {
    --stage: #2b2b2c;
    --paper: #f7f7f7;
    --teal: #17b3b4;
    --teal-deep: #0fa3a6;
    --navy: #1b2557;
    --navy-soft: #25306a;
    --grey: #a9abae;
    --white: #ffffff;
  }
  * { box-sizing: border-box; margin: 0; padding: 0; }
  html, body {
    width: 1200px; height: 886px; overflow: hidden;
    background: var(--stage);
    font-family: "Roboto", Arial, sans-serif;
  }
  .stage {
    width: 1200px; height: 886px;
    display: flex; flex-direction: column;
    align-items: center; justify-content: center; gap: 46px;
  }
  .card {
    width: 700px; height: 400px;
    border-radius: 26px;
    position: relative; overflow: hidden;
    box-shadow: 0 18px 40px rgba(0,0,0,0.45);
  }

  /* Side one */
  .card-front {
    background: var(--paper);
    display: flex; flex-direction: column;
    align-items: center; justify-content: center;
  }
  .brand {
    display: flex; align-items: center; gap: 16px;
  }
  .brand-dot {
    width: 34px; height: 34px; border-radius: 50%;
    background: var(--teal);
  }
  .brand-name {
    font-family: "Roboto Condensed", Arial, sans-serif;
    font-weight: 700; font-size: 50px; letter-spacing: 1px;
    color: var(--navy);
  }
  .tagline-row {
    margin-top: 42px;
    display: flex; align-items: center; gap: 14px;
  }
  .tagline-rule {
    width: 110px; height: 1px; background: var(--navy);
    opacity: 0.7;
  }
  .tagline {
    font-style: italic; font-size: 19px; color: var(--navy);
  }
  .tagline .accent { color: var(--teal); }

  /* Side two */
  .card-back {
    background: linear-gradient(135deg, var(--navy-soft), var(--navy));
  }
  .back-panel {
    position: absolute; left: 0; top: 0; width: 330px; height: 100%;
    background: linear-gradient(160deg, var(--teal), var(--teal-deep));
  }
  .back-arc {
    position: absolute; left: 300px; top: 0; width: 60px; height: 400px;
  }
  .holder {
    position: absolute; left: 44px; top: 48px;
    color: var(--white);
  }
  .holder-name {
    font-family: "Roboto Condensed", Arial, sans-serif;
    font-weight: 700; font-size: 38px; letter-spacing: 0.5px;
  }
  .holder-role {
    font-family: "Roboto Condensed", Arial, sans-serif;
    font-size: 15px; letter-spacing: 2px; margin-top: 4px;
    text-align: right;
  }
  .contact {
    position: absolute; right: 52px; bottom: 56px;
    list-style: none; color: var(--white);
    font-size: 19px; line-height: 1.55;
  }
  .contact-label {
    color: var(--teal); font-weight: 700; margin-right: 6px;
  }
</style>
</head>
<body>
<main class="stage">
  <section class="card card-front" aria-label="Card side one">
    <div class="brand">
      <span class="brand-dot"></span>
      <span class="brand-name">BRIGHTWAY HAUS INC.</span>
    </div>
    <div class="tagline-row">
      <span class="tagline-rule"></span>
      <span class="tagline">Where <span class="accent">Shine</span> Counts</span>
      <span class="tagline-rule"></span>
    </div>
  </section>

  <section class="card card-back" aria-label="Card side two">
    <div class="back-panel"></div>
    <svg class="back-arc" viewBox="0 0 60 400" aria-hidden="true">
      <path d="M30 0 Q60 200 30 400 L0 400 L0 0 Z" fill="#0fa3a6"/>
    </svg>
    <div class="holder">
      <p class="holder-name">DANA MERCER</p>
      <p class="holder-role">OWNER</p>
    </div>
    <ul class="contact">
      <li><span class="contact-label">P:</span>905 555 0142</li>
      <li><span class="contact-label">E:</span>dana@thebrightwayhaus.ca</li>
      <li><span class="contact-label">W:</span>www.thebrightwayhaus.ca</li>
    </ul>
  </section>
</main>
</body>
</html>
```